Internal web page of multinational company - Portfolio of reports

We need to improve the look & feel of an existing internal HTML page.
We use it as a portfolios where users go and see a list of existing reports as "tiles". The HTML page is automatically generated by a javascript that reads the contents to display from an HTML file.
What is needs is a "face lift" in the design of the page.
Currently we use icons on the top right of each tile to denote the type of technology used on the report and also colons for the same purpose. The attached screenshots will be self explanatory.
Across the top we have "tabs" that, once selected change the tiles.
Need a proposal for new design that keeps is as clean as possible, specially the home page that should be very light (Plimbo like).
The idea for this page is to serve as a "one stop shop" and become a bookmark for everyone in the company.
Looking for a wow effect that make is visually

Target Market(s)

Internal employees

Industry/Entity Type

It Company

Coding

Coded - Design and coding required

Number of Pages Required

2 page

Requirements
Must have
• Should not change the logo or its position from the bottom left.
• Page must be as clean as possible and
Nice to have
• Welcome to change the logo on the top left. This page is from the CSU M&I (Mni) which stands for Central Support Unit - Metrics & Insight.
Should not have
• Do no use red, this is the color of our competitor. The blue on the bottom is standard for our logo

```html
<!DOCTYPE html>
<html lang="en">
<head>
<meta charset="utf-8">
<title>CSU M&amp;I – Solutions Portfolio</title>
<link rel="stylesheet" href="https://fonts.googleapis.com/css2?family=Oswald:wght@400&family=Ubuntu:wght@400;700&family=Open+Sans:wght@400&display=swap">
<style>
  :root {
    --navy: #0a2a85;
    --brand-blue: #5069a3;
    --icon-blue: #4b65a2;
    --ink: #2b2b2b;
    --white: #ffffff;
    --line: #dcdcdc;
    --tile-bg: rgba(255,255,255,0.78);
    --tile-border: #e0e2e8;
  }
  * { box-sizing: border-box; margin: 0; padding: 0; }
  html, body { width: 1200px; height: 715px; overflow: hidden; }
  body { font-family: "Open Sans", Arial, sans-serif; color: var(--ink); position: relative; background: var(--white); }

  .site-header {
    position: absolute; left: 0; top: 0; width: 1200px; height: 111px;
    background: var(--white); box-shadow: 0 1px 4px rgba(0,0,0,0.12); z-index: 2;
  }
  .brand { position: absolute; left: 99px; top: 28px; display: flex; align-items: center; gap: 12px; }
  .brand-mark { width: 61px; height: 61px; border-radius: 50%; background: var(--navy); }
  .brand-name { font-family: "Oswald", sans-serif; font-size: 42px; line-height: 1; color: var(--ink); letter-spacing: 0.5px; }

  .search { position: absolute; left: 779px; top: 39px; display: flex; gap: 9px; }
  .search-field {
    width: 226px; height: 36px; border: 1px solid var(--line); border-radius: 3px;
    font: 13px "Open Sans", sans-serif; color: #555; padding: 0 12px; display: flex; align-items: center;
  }
  .search-buttons { display: flex; border: 1px solid var(--line); border-radius: 3px; height: 36px; }
  .search-btn { width: 44px; display: flex; align-items: center; justify-content: center; font: 700 14px "Open Sans", sans-serif; color: #555; }
  .search-btn + .search-btn { border-left: 1px solid var(--line); }

  .hero {
    position: absolute; left: 0; top: 111px; width: 1200px; height: 530px;
    background: linear-gradient(180deg, #f7f7f9 0%, #f2f3f6 45%, #e6e9f0 100%);
  }
  .hero-title {
    position: absolute; left: 0; width: 100%; top: 104px; text-align: center;
    font-family: "Ubuntu", sans-serif; font-weight: 700; font-size: 52px; color: var(--navy); letter-spacing: 1px;
  }
  .hero-subtitle {
    position: absolute; left: 0; width: 100%; top: 177px; text-align: center;
    font-family: "Ubuntu", sans-serif; font-size: 31px; color: var(--navy);
  }
  .tiles { position: absolute; top: 288px; left: 99px; display: flex; gap: 15px; }
  .tile {
    width: 188px; height: 156px; background: var(--tile-bg); border: 1px solid var(--tile-border);
    border-radius: 4px; box-shadow: 0 1px 3px rgba(0,0,0,0.08);
    display: flex; flex-direction: column; align-items: center; padding-top: 30px;
  }
  .tile.is-active { box-shadow: inset 0 0 22px rgba(0,0,0,0.08), 0 1px 4px rgba(0,0,0,0.15); }
  .tile svg { width: 66px; height: 66px; }
  .tile-label { margin-top: 10px; font-family: "Open Sans", sans-serif; font-size: 15px; color: var(--icon-blue); }

  .site-footer {
    position: absolute; left: 0; top: 641px; width: 1200px; height: 74px; background: var(--brand-blue); color: var(--white);
  }
  .copyright { position: absolute; left: 97px; top: 28px; font-size: 12px; }
  .social { position: absolute; left: 556px; top: 27px; display: flex; gap: 4px; }
  .social-btn { width: 20px; height: 20px; border-radius: 3px; background: var(--white); display: flex; align-items: center; justify-content: center; }
  .help { position: absolute; left: 928px; top: 24px; display: flex; align-items: center; gap: 7px; font-family: "Open Sans", sans-serif; font-size: 15px; }
  .version { position: absolute; left: 1160px; top: 29px; font-size: 11px; }
</style>
</head>
<body>
  <header class="site-header">
    <div class="brand">
      <span class="brand-mark"></span>
      <span class="brand-name">CSU M&amp;I</span>
    </div>
    <div class="search">
      <div class="search-field">Search</div>
      <div class="search-buttons">
        <span class="search-btn">
          <svg width="14" height="14" viewBox="0 0 14 14"><circle cx="6" cy="6" r="4.3" fill="none" stroke="#888" stroke-width="2"/><line x1="9" y1="9" x2="12.5" y2="12.5" stroke="#888" stroke-width="2.2" stroke-linecap="round"/></svg>
        </span>
        <span class="search-btn">X</span>
      </div>
    </div>
  </header>

  <main class="hero" role="img" aria-label="Faded city skyline photograph behind the portfolio">
    <h1 class="hero-title">SOLUTIONS PORTFOLIO</h1>
    <p class="hero-subtitle">Shared Services</p>

    <nav class="tiles">
      <div class="tile is-active">
        <svg viewBox="0 0 66 66">
          <circle cx="27" cy="27" r="19" fill="none" stroke="#4b65a2" stroke-width="7"/>
          <circle cx="27" cy="27" r="14" fill="#4b65a2"/>
          <path d="M18 20 q6 -5 12 0 q-2 6 -7 6 q0 6 -4 8 q-3 -6 -1 -14z M31 30 q5 -2 6 4 q-3 5 -6 2z" fill="#fff"/>
          <line x1="41" y1="41" x2="58" y2="58" stroke="#4b65a2" stroke-width="8" stroke-linecap="round"/>
        </svg>
        <span class="tile-label">HR SERVICE</span>
      </div>
      <div class="tile">
        <svg viewBox="0 0 66 66">
          <circle cx="30" cy="36" r="26" fill="#4b65a2"/>
          <circle cx="30" cy="36" r="19" fill="#fff"/>
          <circle cx="30" cy="36" r="13" fill="#4b65a2"/>
          <circle cx="30" cy="36" r="6" fill="#fff"/>
          <line x1="30" y1="36" x2="56" y2="10" stroke="#4b65a2" stroke-width="4"/>
          <path d="M52 4 l2 8 l8 2 l-6 6 l-8 -2 l-2 -8z" fill="#4b65a2"/>
        </svg>
        <span class="tile-label">FINANCE</span>
      </div>
      <div class="tile">
        <svg viewBox="0 0 66 66">
          <g fill="#4b65a2">
            <circle cx="42" cy="22" r="15"/>
            <g transform="translate(42 22)"><rect x="-4" y="-21" width="8" height="42"/><rect x="-4" y="-21" width="8" height="42" transform="rotate(45)"/><rect x="-4" y="-21" width="8" height="42" transform="rotate(90)"/><rect x="-4" y="-21" width="8" height="42" transform="rotate(135)"/></g>
            <circle cx="15" cy="50" r="9"/>
            <g transform="translate(15 50)"><rect x="-2.5" y="-13" width="5" height="26"/><rect x="-2.5" y="-13" width="5" height="26" transform="rotate(45)"/><rect x="-2.5" y="-13" width="5" height="26" transform="rotate(90)"/><rect x="-2.5" y="-13" width="5" height="26" transform="rotate(135)"/></g>
            <circle cx="38" cy="54" r="6"/>
            <g transform="translate(38 54)"><rect x="-2" y="-9" width="4" height="18"/><rect x="-2" y="-9" width="4" height="18" transform="rotate(60)"/><rect x="-2" y="-9" width="4" height="18" transform="rotate(120)"/></g>
          </g>
          <circle cx="42" cy="22" r="6" fill="#fff"/><circle cx="15" cy="50" r="3.5" fill="#fff"/><circle cx="38" cy="54" r="2.5" fill="#fff"/>
        </svg>
        <span class="tile-label">P&amp;S</span>
      </div>
      <div class="tile">
        <svg viewBox="0 0 66 66">
          <circle cx="33" cy="33" r="31" fill="#4b65a2"/>
          <path d="M10 22 q8 -12 18 -6 q-2 8 -9 9 q2 9 -4 14 q-6 -6 -5 -17z M36 8 q10 2 16 10 q-8 2 -12 -2z M38 34 q10 -4 16 4 q0 12 -10 16 q-8 -8 -6 -20z M22 50 q6 2 8 8 q-6 0 -8 -8z" fill="#fff"/>
        </svg>
        <span class="tile-label">CSU</span>
      </div>
      <div class="tile">
        <svg viewBox="0 0 66 66">
          <g fill="none" stroke="#4b65a2" stroke-width="6">
            <path d="M22 10 a26 26 0 0 1 28 4"/>
            <path d="M59 33 a26 26 0 0 1 -14 23"/>
            <path d="M24 58 a26 26 0 0 1 -17 -24"/>
          </g>
          <g fill="#4b65a2">
            <path d="M46 6 l10 12 l-14 2z"/>
            <path d="M52 60 l-16 -2 l10 -10z"/>
            <path d="M0 28 l14 -6 l-2 14z"/>
          </g>
        </svg>
        <span class="tile-label">DISTRIBUTION</span>
      </div>
    </nav>
  </main>

  <footer class="site-footer">
    <p class="copyright">(c) 2015 CSU M&amp;I. All rights reserved.</p>
    <div class="social">
      <span class="social-btn"></span>
      <span class="social-btn"></span>
      <span class="social-btn"></span>
      <span class="social-btn">
        <svg width="14" height="14" viewBox="0 0 14 14"><path d="M3 1 l3 3 l-1.5 2 q1 2.5 3.5 3.5 l2 -1.5 l3 3 l-2 2 q-6 0 -10 -10z" fill="#5069a3"/></svg>
      </span>
    </div>
    <div class="help">
      <span>HELP &amp; FEEDBACK</span>
      <svg width="38" height="32" viewBox="0 0 38 32">
        <path d="M3 1 h32 a2 2 0 0 1 2 2 v21 a2 2 0 0 1 -2 2 h-15 l-5 5 v-5 h-12 a2 2 0 0 1 -2 -2 v-21 a2 2 0 0 1 2 -2z" fill="none" stroke="#fff" stroke-width="1.5"/>
        <text x="19" y="19" text-anchor="middle" font-family="Open Sans, sans-serif" font-size="14" font-weight="700" fill="#fff">?</text>
      </svg>
    </div>
    <span class="version">C7</span>
  </footer>
</body>
</html>
```